Business Card Design

Printing and photocopying solutions, computer sales, photocopier sales and service, stationery needs

We aim to be the best for reliability, knowledge, skilled technical ability and highly ethical in business dealings. We would like to present as professional and the key person for dealing with for all customers. We are based in the Solomon Islands and therefore part of a developing country where many services and infrastructures are not in place. We would like to be seen as leading the field with technology and advanced office support. We strongly support the community and education systems with our current services and are seeking to expand the reach to encompass other service offerings

Target Market(s)

Business, Schools, Government offices, Churches, Non-government organisations

Industry/Entity Type

Business

Contact Information for Business Card

Harbourlight Print
harbourlightprint@mailvane.example
+677 7418062 +677 8205147
PO Box 8
Auki, Malaita Province
Solomon Islands

Requirements
Must have
• professional appearance. Some Blue colouring
Must have easy to read phone number so required the phone number to be large font

Must have Shop address as well
Shop 7, Tidewell Building
Auki, Malaita, Solomon Islands
Nice to have
• Keep simple and professional with appearance of the business card styles, use the back of the card for Logo and a list of the basic services that is offered from Harbourlight Print

```html
<!DOCTYPE html>
<html lang="en">
<head>
<meta charset="utf-8">
<title>Harbourlight Print – Business Card</title>
<link rel="stylesheet" href="https://fonts.googleapis.com/css2?family=Jura:wght@500;600;700&family=Open+Sans:wght@400;600&display=swap">
<style>
  :root {
    --page-bg: #2b2c2f;
    --card-white: #f6f6f6;
    --card-grey: #d9d9db;
    --band-dark: #24272e;
    --band-deep: #17191e;
    --brand-blue: #1f5fd6;
    --ink: #2a2a2a;
    --ink-soft: #4a4a4a;
    --rule: #b8b8bc;
  }
  * { margin: 0; padding: 0; box-sizing: border-box; }
  html, body { width: 1200px; height: 816px; overflow: hidden; }
  body { background: var(--page-bg); position: relative; }

  .business-card {
    position: absolute;
    left: 100px; top: 108px;
    width: 1000px; height: 600px;
    border-radius: 56px;
    overflow: hidden;
    box-shadow: 0 18px 40px rgba(0,0,0,.35);
  }
  .card-shapes { position: absolute; inset: 0; display: block; }

  .brand {
    position: absolute;
    left: 240px; top: 0; width: 392px; height: 250px;
    display: flex; align-items: center; justify-content: center; gap: 12px;
    padding-top: 30px;
  }
  .brand-mark { width: 16px; height: 16px; background: var(--brand-blue); flex: none; }
  .brand-name {
    font-family: "Jura", sans-serif; font-weight: 700;
    font-size: 32px; color: var(--brand-blue); white-space: nowrap;
  }

  .holder {
    position: absolute; right: 400px; top: 396px; text-align: right;
    font-family: "Jura", sans-serif; color: var(--ink);
  }
  .holder-name { font-size: 40px; font-weight: 700; letter-spacing: 1px; line-height: 1; }
  .holder-role { font-size: 20px; font-weight: 600; margin-top: 8px; letter-spacing: .5px; }

  .divider {
    position: absolute; left: 615px; top: 318px;
    width: 1px; height: 188px; background: var(--rule);
  }
  .contact-list {
    position: absolute; left: 634px; top: 320px; list-style: none;
    font-family: "Open Sans", sans-serif; font-size: 15px; color: var(--ink-soft);
    line-height: 24px; white-space: nowrap;
  }
  .contact-phone {
    font-family: "Jura", sans-serif; font-weight: 700;
    font-size: 27px; line-height: 32px; color: var(--ink);
  }
  .contact-email { margin-top: 4px; }
</style>
</head>
<body>
  <section class="business-card">
    <svg class="card-shapes" viewBox="0 0 1000 600" width="1000" height="600">
      <defs>
        <linearGradient id="card-face" x1="0" y1="0" x2="0" y2="1">
          <stop offset="0" stop-color="var(--card-white)"/>
          <stop offset="1" stop-color="var(--card-grey)"/>
        </linearGradient>
        <linearGradient id="band-fill" x1="0" y1="0" x2="1" y2="1">
          <stop offset="0" stop-color="var(--band-dark)"/>
          <stop offset="1" stop-color="var(--band-deep)"/>
        </linearGradient>
      </defs>
      <rect class="card-face" width="1000" height="600" fill="url(#card-face)"/>
      <rect class="upper-band" x="22" y="30" width="956" height="270" rx="40" fill="url(#band-fill)"
            role="img" aria-label="Dark band with a hexagon pattern"/>
      <path class="logo-tab" fill="var(--card-white)"
            d="M0 0 L690 0 L690 30 Q632 30 632 88 L632 192 Q632 250 574 250 L298 250 Q240 250 240 192 L240 180 Q240 130 180 130 L0 130 Z"/>
      <rect class="lower-stripe" x="22" y="522" width="956" height="48" rx="24" fill="url(#band-fill)"
            role="img" aria-label="Dark stripe with a hexagon pattern"/>
      <rect class="card-edge" x="4" y="4" width="992" height="592" rx="52" fill="none" stroke="#ffffff" stroke-width="8"/>
    </svg>

    <div class="brand">
      <span class="brand-mark"></span>
      <span class="brand-name">Harbourlight Print</span>
    </div>

    <div class="holder">
      <p class="holder-name">Daniel Rowe</p>
      <p class="holder-role">Direction &amp; Ceo</p>
    </div>

    <span class="divider"></span>
    <ul class="contact-list">
      <li class="contact-phone">+677 7418062</li>
      <li class="contact-phone">+677 8205147</li>
      <li class="contact-email">harbourlightprint@mailvane.example</li>
      <li>PO Box 8, Auki, Malaita Province</li>
      <li>Shop 7, Tidewell Building</li>
      <li>Auki, Malaita, Solomon Islands</li>
    </ul>
  </section>
</body>
</html>
```